Commercial/Corporate Law Firm needs Website Design

Hi guys. I've started up a new law firm and would love your help designing an attractive website. I'll need both design and coding, and to make it easy for us to edit as necessary later, I think it should be built off a Wordpress.org structure.
FIRST IMPRESSIONS
It's very important that the first impression of the website really captures our prospective clients' attention and impresses them. Their first three seconds needs to be good.
I imagine the homepage may be short, with a menu bar and a compelling image, and with a tagline overlaid or underneath (eg. "It's about results.")
The image should be related to our practice areas: eg. IPOs, corporate transactions, or commercial negotiations.
I have previously suggested there could be a skyline image of Sydney or Adelaide. However, because we are based in Adelaide, I don't think Sydney is appropriate - and Adelaide is probably too boring to use.
HOMEPAGE
Being a new firm, we don't have many existing testimonials, and I will be the only lawyer to start with. So we need to focus on the nature of the services we will provide and how my experience can help them. We have an existing logo to use, and I would like the website colour scheme not to clash with that logo (dark blue and white).
After the initial image and tagline there should be a brief introduction to each of the main areas of work, eg. "We specialise in three main areas of practice:"
1. Corporate Transactions and Regulation
2. Business Law and Dispute Resolution
3. Migration Assistance
These should each have an appropriate photo and link to a separate page that briefly describes our services in that area.
Below that there should be a message from me with a photo. Finally, at the bottom, there should be a "Contact Us" section which shows a Google image of our address, contact details, and then our logo with colours inverted.
OTHER PAGES
While we will need some other pages, they should all be fairly simple. I think we will need one page to say "About Us", where I will put information about my experience. I think we will then need one page for each of the 3 areas listed above, which just needs an appropriate image and then text to describe the service. Finally, a "Contact Us" page which I imagine will be the same as the bottom of the homepage.
OTHER DETAILS
For now you can use details from my LinkedIn page to fill out any other text as necessary, or the photo.
Because the logo is square, I would prefer the design of the website also to be rectangular.
Looking forward to seeing your work! Thank you.
Marcus
Potential clients:
Businesses with legal issues or disputes
Companies wishing to list on the stock market

```html
<!DOCTYPE html>
<html lang="en">
<head>
<meta charset="utf-8">
<title>Hartwell Legal</title>
<link href="https://fonts.googleapis.com/css2?family=Cinzel:wght@600;700&family=Montserrat:wght@400;600;700&family=Open+Sans:wght@400;600&display=swap" rel="stylesheet">
<style>
:root{
  --navy:#0b2a5c;
  --blue:#0a62c9;
  --text:#4a4f5a;
  --grey-panel:#f1f2f4;
  --footer-bar:#0d2450;
  --white:#ffffff;
}
*{box-sizing:border-box;margin:0;padding:0}
html,body{width:1200px;height:3502px;overflow:hidden;background:var(--white)}
body{position:relative;font-family:"Open Sans",Arial,sans-serif;color:var(--text)}
.abs{position:absolute}
.photo{position:absolute}

/* header */
.site-header{position:absolute;left:0;top:0;width:1200px;height:157px;background:var(--white)}
.brand{position:absolute;left:60px;top:34px;width:190px;text-align:center;font-family:"Montserrat",sans-serif;font-weight:600;color:var(--navy);font-size:24px;letter-spacing:3px;line-height:1.2}
.brand .mark{display:block;width:50px;height:50px;background:var(--navy);margin:0 auto 8px}
.nav a{position:absolute;top:63px;font-family:"Montserrat",sans-serif;font-size:15px;color:#6a6f78;text-decoration:none;letter-spacing:.5px}
.btn{display:inline-block;background:var(--blue);color:var(--white);font-family:"Montserrat",sans-serif;font-size:16px;text-align:center;text-decoration:none}
.nav .btn-consult{position:absolute;left:817px;top:47px;width:208px;height:52px;line-height:52px;font-size:15px;color:#fff}

/* hero */
.hero{position:absolute;left:0;top:157px;width:1200px;height:572px;
  background:
    radial-gradient(ellipse 420px 260px at 600px 200px,rgba(210,214,218,.35),rgba(210,214,218,0) 70%),
    radial-gradient(ellipse 300px 220px at 180px 150px,rgba(190,196,204,.3),rgba(190,196,204,0) 70%),
    radial-gradient(ellipse 320px 240px at 1020px 170px,rgba(200,204,210,.28),rgba(200,204,210,0) 70%),
    linear-gradient(180deg,#6a7076 0%,#40454b 35%,#22262a 62%,#0d0e10 100%)}
.hero-mark{position:absolute;left:563px;top:140px;width:74px;height:74px;background:#fff}
.hero h1{position:absolute;left:0;width:1200px;top:228px;text-align:center;font-family:"Montserrat",sans-serif;font-weight:700;font-size:40px;color:#fff;letter-spacing:1px}
.hero p{position:absolute;left:300px;width:600px;top:285px;text-align:center;font-size:14.5px;line-height:23px;color:#ececec}
.hero .btn{position:absolute;left:517px;top:353px;width:166px;height:60px;line-height:60px}
.hero-arrow{position:absolute;top:261px;width:50px;height:50px;border-radius:50%}

/* practice */
.section-title{position:absolute;left:0;width:1200px;text-align:center;font-family:"Cinzel",serif;font-weight:700;font-size:36px;color:var(--navy)}
.intro{position:absolute;left:100px;width:1000px;text-align:center;font-size:13.5px;line-height:28px;color:var(--text)}
.practice-card{position:absolute;top:947px;width:334px}
.practice-card .photo{position:relative;width:334px;height:220px}
.practice-head{display:flex;align-items:center;gap:14px;margin-top:28px;height:50px}
.practice-head h3{font-family:"Montserrat",sans-serif;font-weight:700;font-size:16px;color:var(--navy);line-height:24px}
.practice-card p{margin-top:18px;font-size:13.5px;line-height:27px;color:var(--text)}

/* features */
.features{position:absolute;left:0;top:1417px;width:600px;height:468px;background:var(--grey-panel)}
.feature{position:absolute;width:240px}
.feature h4{margin-top:16px;font-family:"Montserrat",sans-serif;font-weight:700;font-size:15px;color:var(--navy)}
.feature p{margin-top:8px;font-size:13.5px;line-height:27px}

/* news */
.news-card{position:absolute;top:2030px;width:334px;height:480px;background:#fff;box-shadow:0 2px 14px rgba(0,0,0,.14)}
.news-card .photo{left:10px;top:13px;width:314px;height:207px}
.tag{position:absolute;left:100px;top:200px;width:134px;height:42px;line-height:42px;background:var(--blue);color:#fff;text-align:center;font-family:"Montserrat",sans-serif;font-size:13px}
.news-card h3{position:absolute;left:20px;width:294px;top:260px;text-align:center;font-family:"Montserrat",sans-serif;font-weight:700;font-size:16px;line-height:25px;color:var(--navy)}
.news-card p{position:absolute;left:25px;width:284px;top:318px;text-align:center;font-size:13.5px;line-height:27px}
.news-card time{position:absolute;left:0;width:334px;top:413px;text-align:center;font-family:"Montserrat",sans-serif;font-size:13px;font-weight:600;color:var(--navy)}
.read-line{position:absolute;left:599px;top:2488px;width:3px;height:46px;background:var(--blue)}
.read-more{position:absolute;left:0;width:1200px;top:2546px;text-align:center;font-family:"Montserrat",sans-serif;font-weight:700;font-size:13px;color:var(--navy)}
.dots{position:absolute;left:572px;top:2594px;display:flex;gap:10px}
.dots span{width:10px;height:10px;border:2px solid var(--navy)}
.dots span.on{background:var(--navy);width:14px;height:14px;margin-top:-2px}

/* about */
.about-title{position:absolute;left:557px;top:2683px;font-family:"Cinzel",serif;font-weight:700;font-size:36px;color:var(--navy)}
.about-text{position:absolute;left:557px;top:2750px;width:575px;font-size:13.5px;line-height:28px}
.about .btn{position:absolute;left:557px;top:2965px;width:165px;height:60px;line-height:60px;font-size:18px}

/* footer */
.site-footer{position:absolute;left:0;top:3095px;width:1200px;height:345px;
  background:
    radial-gradient(ellipse 500px 200px at 900px 300px,rgba(80,90,105,.35),rgba(80,90,105,0) 70%),
    linear-gradient(180deg,#202226,#15171a 60%,#1b1e23)}
.foot-brand{position:absolute;left:95px;top:58px;width:170px;text-align:center;font-family:"Montserrat",sans-serif;font-weight:600;color:#fff;font-size:20px;letter-spacing:3px;line-height:1.2}
.foot-brand .mark{display:block;width:42px;height:42px;background:#fff;margin:0 auto 8px}
.foot-about{position:absolute;left:77px;top:172px;width:210px;text-align:center;color:#e6e6e6;font-size:13.5px;line-height:25px}
.foot-col h4{position:absolute;top:62px;font-family:"Cinzel",serif;font-weight:600;font-size:17px;color:var(--blue);letter-spacing:.5px}
.contact-list{position:absolute;left:345px;top:122px;width:230px;list-style:none;color:#e6e6e6;font-size:13.5px;line-height:26px}
.contact-list b{color:#fff}
.practice-list{position:absolute;left:596px;top:118px;width:220px;list-style:none;color:#e6e6e6;font-size:13.5px;line-height:26px}
.practice-list li{position:relative;padding-left:22px;margin-bottom:10px}
.practice-list li::before{content:"";position:absolute;left:0;top:10px;width:7px;height:7px;border-radius:50%;background:#fff}
.news-text{position:absolute;left:872px;top:120px;width:255px;color:#e6e6e6;font-size:13.5px;line-height:26px}
.signup{position:absolute;left:872px;top:210px;width:250px;height:50px;display:flex}
.signup .field{flex:1;background:#fff;font-size:13px;color:#555;padding:15px 14px}
.signup .send{width:62px;background:var(--blue);display:flex;align-items:center;justify-content:center}
.footer-bar{position:absolute;left:0;top:3440px;width:1200px;height:62px;background:var(--footer-bar);border-top:3px solid var(--blue)}
.footer-bar p{position:absolute;left:77px;top:20px;color:#e6e6e6;font-size:13px}
.footer-bar b{color:#fff}
.social{position:absolute;top:12px;width:36px;height:36px;border:1px solid #8aa0c6}
.social span{position:absolute;left:11px;top:11px;width:12px;height:12px;background:#fff}
</style>
</head>
<body>

<header class="site-header">
  <div class="brand"><span class="mark"></span>HARTWELL<br><span style="font-size:13px;letter-spacing:6px">LEGAL</span></div>
  <nav class="nav">
    <a style="left:326px">HOME</a>
    <a style="left:418px">ABOUT</a>
    <a style="left:519px">PRACTICE AREAS</a>
    <a style="left:700px">CONTACT</a>
    <a class="btn btn-consult">FREE CONSULTATION</a>
  </nav>
  <svg class="abs" style="left:1050px;top:60px" width="26" height="26" viewBox="0 0 26 26"><circle cx="10" cy="10" r="8" fill="none" stroke="#6a6f78" stroke-width="2"/><line x1="16" y1="16" x2="24" y2="24" stroke="#6a6f78" stroke-width="2"/></svg>
  <svg class="abs" style="left:1098px;top:59px" width="24" height="26" viewBox="0 0 24 26"><rect x="1" y="1" width="22" height="24" fill="none" stroke="#333" stroke-width="2"/><line x1="6" y1="8" x2="18" y2="8" stroke="#333" stroke-width="2"/><line x1="6" y1="13" x2="18" y2="13" stroke="#333" stroke-width="2"/><line x1="6" y1="18" x2="18" y2="18" stroke="#333" stroke-width="2"/></svg>
</header>

<section class="hero" role="img" aria-label="Business people shaking hands in a dark office with tall bright windows">
  <div class="hero-mark"></div>
  <h1>IT'S ABOUT RESULTS</h1>
  <p>Lorem ipsum dolor sit amet, consectetur adipiscing elit, sed do eiusmod<br>tempor incididunt ut labore et dolore magna aliqua.</p>
  <a class="btn">CONTACT US</a>
  <svg class="hero-arrow" style="left:50px" viewBox="0 0 50 50"><circle cx="25" cy="25" r="25" fill="var(--blue)"/><polyline points="28,18 21,25 28,32" fill="none" stroke="#fff" stroke-width="3"/></svg>
  <svg class="hero-arrow" style="left:1096px" viewBox="0 0 50 50"><circle cx="25" cy="25" r="25" fill="#e9e9e9"/><polyline points="22,18 29,25 22,32" fill="none" stroke="var(--navy)" stroke-width="3"/></svg>
</section>

<section class="practice">
  <h2 class="section-title" style="top:785px">We Are Here To Help!</h2>
  <p class="intro" style="top:850px">Lorem ipsum dolor sit amet, consectetur adipiscing elit, sed do eiusmod tempor incididunt ut labore et dolore magna aliqua.<br>Ut enim ad minim veniam, quis nostrud exercitation ullamco laboris nisi ut aliquip ex ea commodo consequat.</p>

  <article class="practice-card" style="left:77px">
    <div class="photo" role="img" aria-label="Two businessmen shaking hands by a window with a blue city skyline" style="background:radial-gradient(ellipse 200px 160px at 260px 60px,rgba(200,225,250,.7),rgba(200,225,250,0) 70%),linear-gradient(160deg,#9cc4ec 0%,#4f83bd 40%,#2a4f80 70%,#1a2638 100%)"></div>
    <div class="practice-head">
      <svg width="50" height="40" viewBox="0 0 50 40"><circle cx="10" cy="9" r="5" fill="var(--navy)"/><circle cx="25" cy="7" r="5" fill="var(--navy)"/><circle cx="40" cy="9" r="5" fill="var(--navy)"/><rect x="3" y="16" width="14" height="12" rx="3" fill="var(--navy)"/><rect x="18" y="14" width="14" height="14" rx="3" fill="var(--blue)"/><rect x="33" y="16" width="14" height="12" rx="3" fill="var(--navy)"/><rect x="0" y="29" width="50" height="4" fill="var(--navy)"/></svg>
      <h3>Business Law and Dispute<br>Resolution</h3>
    </div>
    <p>Lorem Ipsum is simply dummy text of the printing and typesetting industry. Lorem Ipsum has been the industry's standard dummy text ever since the 1500s.</p>
  </article>

  <article class="practice-card" style="left:432px">
    <div class="photo" role="img" aria-label="Two colleagues reviewing a tablet at a desk" style="background:radial-gradient(ellipse 180px 140px at 90px 150px,rgba(235,225,212,.8),rgba(235,225,212,0) 70%),linear-gradient(135deg,#e2dbd0 0%,#a39686 45%,#5a524a 75%,#2e2b29 100%)"></div>
    <div class="practice-head">
      <svg width="40" height="40" viewBox="0 0 40 40"><circle cx="14" cy="14" r="10" fill="none" stroke="var(--navy)" stroke-width="4"/><path d="M22 22 L34 34" stroke="var(--blue)" stroke-width="4"/><polyline points="26,34 34,34 34,26" fill="none" stroke="var(--blue)" stroke-width="4"/></svg>
      <h3>Corporate Transactions<br>and Regulation</h3>
    </div>
    <p>Lorem Ipsum is simply dummy text of the printing and typesetting industry. Lorem Ipsum has been the industry's standard dummy text ever since the 1500s.</p>
  </article>

  <article class="practice-card" style="left:790px">
    <div class="photo" role="img" aria-label="Businessmen shaking hands across a desk in a bright office" style="background:radial-gradient(ellipse 200px 150px at 80px 50px,rgba(240,248,255,.85),rgba(240,248,255,0) 70%),linear-gradient(135deg,#d8e7f3 0%,#8eaac6 40%,#3d5675 72%,#1c2636 100%)"></div>
    <div class="practice-head">
      <svg width="40" height="40" viewBox="0 0 40 40"><rect x="10" y="3" width="26" height="34" fill="none" stroke="var(--navy)" stroke-width="4"/><line x1="2" y1="20" x2="22" y2="20" stroke="var(--blue)" stroke-width="4"/><polyline points="15,13 22,20 15,27" fill="none" stroke="var(--blue)" stroke-width="4"/></svg>
      <h3>Migration Assistance</h3>
    </div>
    <p>Lorem Ipsum is simply dummy text of the printing and typesetting industry. Lorem Ipsum has been the industry's standard dummy text ever since the 1500s.</p>
  </article>
</section>

<section class="features">
  <div class="feature" style="left:79px;top:60px">
    <svg width="44" height="44" viewBox="0 0 44 44"><path d="M4 20h8v20H4z M14 20 L22 4 c4 0 5 3 4 7 l-2 7 h12 c3 0 4 3 3 5 l-4 15 c-1 2-2 2-4 2 H14z" fill="none" stroke="var(--blue)" stroke-width="3" stroke-linejoin="round"/></svg>
    <h4>Get Legal Advice</h4>
    <p>Lorem Ipsum is simply dummy printing and typesetting industry.</p>
  </div>
  <div class="feature" style="left:340px;top:60px">
    <svg width="44" height="44" viewBox="0 0 44 44"><circle cx="10" cy="10" r="6" fill="var(--blue)"/><circle cx="34" cy="10" r="6" fill="var(--blue)"/><circle cx="22" cy="14" r="6" fill="var(--navy)"/><rect x="3" y="18" width="14" height="18" rx="3" fill="var(--blue)"/><rect x="27" y="18" width="14" height="18" rx="3" fill="var(--blue)"/><rect x="15" y="22" width="14" height="20" rx="3" fill="var(--navy)"/></svg>
    <h4>Expert Lawyer</h4>
    <p>Lorem Ipsum is simply dummy printing and typesetting industry.</p>
  </div>
  <div class="feature" style="left:79px;top:260px">
    <svg width="44" height="44" viewBox="0 0 44 44"><rect x="3" y="12" width="38" height="24" fill="none" stroke="var(--blue)" stroke-width="3" transform="rotate(-10 22 24)"/><circle cx="22" cy="24" r="6" fill="none" stroke="var(--navy)" stroke-width="3"/></svg>
    <h4>Discount Rates</h4>
    <p>Lorem Ipsum is simply dummy printing and typesetting industry.</p>
  </div>
  <div class="feature" style="left:340px;top:260px">
    <svg width="44" height="44" viewBox="0 0 44 44"><rect x="8" y="3" width="26" height="38" fill="none" stroke="var(--blue)" stroke-width="3"/><line x1="14" y1="13" x2="28" y2="13" stroke="var(--navy)" stroke-width="3"/><line x1="14" y1="21" x2="28" y2="21" stroke="var(--navy)" stroke-width="3"/><line x1="14" y1="29" x2="24" y2="29" stroke="var(--navy)" stroke-width="3"/></svg>
    <h4>Review Case Documents</h4>
    <p>Lorem Ipsum is simply dummy printing and typesetting industry.</p>
  </div>
</section>
<div class="photo" role="img" aria-label="Lawyer and colleague reviewing documents together in an office" style="left:600px;top:1417px;width:600px;height:468px;background:radial-gradient(ellipse 260px 220px at 120px 90px,rgba(214,170,120,.55),rgba(214,170,120,0) 70%),radial-gradient(ellipse 240px 200px at 330px 330px,rgba(225,228,235,.45),rgba(225,228,235,0) 70%),linear-gradient(135deg,#a88e72 0%,#5d5a5e 40%,#2f3a4c 70%,#161c26 100%)"></div>

<section class="news">
  <h2 class="section-title" style="top:1940px">Latest News</h2>

  <article class="news-card" style="left:77px">
    <div class="photo" role="img" aria-label="Business people walking outside a columned building" style="background:radial-gradient(ellipse 180px 120px at 220px 60px,rgba(240,236,228,.7),rgba(240,236,228,0) 70%),linear-gradient(135deg,#ddd6ca 0%,#a09889 45%,#5b564f 75%,#2e2c2a 100%)"></div>
    <span class="tag">BUSINESS</span>
    <h3>How to Organize Your Office For Maximum Productivity?</h3>
    <p>Lorem Ipsum is simply dummy text of the printing and typesetting industry. Lorem dummy text ever since the 1500s,</p>
    <time>30 April 2018</time>
  </article>

  <article class="news-card" style="left:432px">
    <div class="photo" role="img" aria-label="Colleagues smiling in a meeting around a table" style="background:radial-gradient(ellipse 200px 130px at 160px 80px,rgba(255,255,255,.8),rgba(255,255,255,0) 70%),linear-gradient(135deg,#f3f1ee 0%,#cbc5bc 45%,#6e675f 78%,#2c2824 100%)"></div>
    <span class="tag">BUSINESS</span>
    <h3>How to Organize Your Office For Maximum Productivity?</h3>
    <p>Lorem Ipsum is simply dummy text of the printing and typesetting industry. Lorem dummy text ever since the 1500s,</p>
    <time>30 April 2018</time>
  </article>

  <article class="news-card" style="left:790px">
    <div class="photo" role="img" aria-label="Business team standing together in an office" style="background:radial-gradient(ellipse 200px 130px at 90px 60px,rgba(245,248,252,.85),rgba(245,248,252,0) 70%),linear-gradient(135deg,#e8ecf2 0%,#a7b3c6 45%,#4c5a72 75%,#1f2736 100%)"></div>
    <span class="tag">BUSINESS</span>
    <h3>How to Organize Your Office For Maximum Productivity?</h3>
    <p>Lorem Ipsum is simply dummy text of the printing and typesetting industry. Lorem dummy text ever since the 1500s,</p>
    <time>30 April 2018</time>
  </article>

  <div class="read-line"></div>
  <div class="read-more">READ MORE</div>
  <div class="dots"><span></span><span class="on"></span><span></span></div>
</section>

<section class="about">
  <div class="photo" role="img" aria-label="Portrait of the principal lawyer in a suit with a night city skyline behind" style="left:77px;top:2690px;width:438px;height:337px;background:radial-gradient(ellipse 140px 200px at 350px 130px,rgba(200,170,110,.45),rgba(200,170,110,0) 70%),radial-gradient(ellipse 150px 190px at 140px 220px,rgba(60,45,60,.6),rgba(60,45,60,0) 70%),linear-gradient(135deg,#3f5a80 0%,#233450 45%,#141c2b 75%,#0a0e15 100%)"></div>
  <h2 class="about-title">About Us</h2>
  <p class="about-text">Lorem Ipsum is simply dummy text of the printing and typesetting industry. Lorem Ipsum has been the industry's standard dummy text ever since the 1500s, when an unknown printer took a galley of type and scrambled it to make a type specimen book. It has survived not only five centuries, but also the leap into electronic typesetting, remaining essentially unchanged. It was popularised in the 1960s with the release of Letraset sheets containing Lorem Ipsum passages, and more recently with desktop publishing software like Aldus PageMaker including versions of Lorem Ipsum.</p>
  <a class="btn">READ MORE</a>
</section>

<footer class="site-footer" role="img" aria-label="Faint night city skyline behind the footer">
  <div class="foot-brand"><span class="mark"></span>HARTWELL<br><span style="font-size:12px;letter-spacing:6px">LEGAL</span></div>
  <p class="foot-about">Lorem Ipsum is simply dummy text of the printing and Print typesetting industry.</p>

  <div class="foot-col"><h4 style="left:345px">Contact Us</h4></div>
  <ul class="contact-list">
    <li><b>A</b> - 123 , Building , street ,<br>&nbsp;&nbsp;&nbsp;&nbsp;&nbsp;State ,Road , Pinacode</li>
    <li style="margin-top:8px"><b>P</b> - <b>0100 555 274</b></li>
    <li style="margin-top:4px"><b>E</b> - <b>info@hartwelllegal.com</b></li>
  </ul>

  <div class="foot-col"><h4 style="left:596px">Our Practice Area</h4></div>
  <ul class="practice-list">
    <li>Corporate Transactions and Regulation</li>
    <li>Business Law and Dispute Resolution</li>
    <li>Migration Assistance</li>
  </ul>

  <div class="foot-col"><h4 style="left:872px">Newsletter</h4></div>
  <p class="news-text">Lorem Ipsum is simply dummy text of the printing and typesetting industry. Lorem Ipsum has been industry's.</p>
  <div class="signup">
    <div class="field">Email</div>
    <div class="send"><svg width="22" height="20" viewBox="0 0 22 20"><polygon points="0,8 22,0 16,20 10,12" fill="#fff"/></svg></div>
  </div>
</footer>

<div class="footer-bar">
  <p>© Copyright 2018, <b>HARTWELL LEGAL</b> . All rights reserved.</p>
  <div class="social" style="left:975px"><span></span></div>
  <div class="social" style="left:1022px"><span></span></div>
  <div class="social" style="left:1070px"><span></span></div>
</div>

</body>
</html>
```